Talvique Hotels Business Card and Logo

We need a business card design for a hotel group. I saw a hotel card you designed and really liked it. We have multiple properties with different brands. Were hoping that the card would be unique and find a way to list out all our properties. Our web address is www.talviquehotels.com. I have attached some photos of card designs I like.

Industry/Entity Type

Hotel

Contact Information for Business Card

Scott CurranReneson HotelsChief Operating Officer56 Madera DriveCorte Madera, CA 94925Office 415-891-5013Cell 707-5550143

```html
<!DOCTYPE html>
<html lang="en">
<head>
<meta charset="utf-8">
<title>Talvique Hotels Business Card</title>
<link rel="stylesheet" href="https://fonts.googleapis.com/css2?family=Cinzel:wght@500&family=Montserrat:wght@400;500&display=swap">
<style>
  :root {
    --stage: #1c1c1c;
    --card-dark: #0c3659;
    --card-light: #1b4b70;
    --ink: #ffffff;
    --accent: #7cb342;
  }
  html, body {
    margin: 0;
    width: 1200px;
    height: 900px;
    overflow: hidden;
    background: var(--stage);
  }
  .canvas {
    width: 1200px;
    height: 900px;
    display: flex;
    flex-direction: column;
    align-items: center;
    justify-content: center;
    gap: 40px;
  }
  .card {
    width: 660px;
    height: 377px;
    background: linear-gradient(160deg, var(--card-dark) 0%, var(--card-light) 70%, var(--card-dark) 100%);
    position: relative;
    box-sizing: border-box;
    color: var(--ink);
    overflow: hidden;
  }
  .brand {
    font-family: "Cinzel", serif;
    font-weight: 500;
    letter-spacing: 0.08em;
    color: var(--ink);
    white-space: nowrap;
  }
  .card--front {
    display: flex;
    align-items: center;
    justify-content: center;
  }
  .card--front .brand { font-size: 44px; }
  .card--back {
    display: flex;
    align-items: center;
    padding: 0 20px 0 30px;
  }
  .card--back .brand {
    flex: none;
    font-size: 25px;
    width: 260px;
    text-align: center;
  }
  .divider {
    flex: none;
    width: 2px;
    height: 220px;
    background: var(--accent);
    margin: 0 22px 0 14px;
  }
  .contact {
    flex: 1;
    min-width: 0;
    font-family: "Montserrat", sans-serif;
    font-size: 15px;
    line-height: 1.4;
    letter-spacing: 0.03em;
  }
  .contact p { margin: 0; }
  .contact__name {
    color: var(--accent);
    font-weight: 500;
    font-size: 20px;
    line-height: 1.15;
    white-space: nowrap;
  }
  .contact .contact__title {
    margin: 2px 0 12px;
    font-size: 14px;
  }
  .contact .contact__address { margin: 0 0 10px; }
  .contact__list { list-style: none; margin: 0; padding: 0; }
  .contact__list li {
    display: flex;
    align-items: center;
    gap: 10px;
    white-space: nowrap;
  }
  .contact__list svg {
    width: 12px;
    height: 12px;
    flex: none;
    stroke: var(--accent);
    fill: none;
    stroke-width: 1.6;
  }
</style>
</head>
<body>
<main class="canvas">
  <section class="card card--front">
    <div class="brand">Talvique Hotels</div>
  </section>

  <section class="card card--back">
    <div class="brand">Talvique Hotels</div>
    <div class="divider"></div>
    <div class="contact">
      <p class="contact__name">Brent Holloway Talvique</p>
      <p class="contact__title">Hotels Chief Operating Officer</p>
      <p class="contact__address">83 Pellwick Lane<br>Larchmont Bay, CA 94990</p>
      <ul class="contact__list">
        <li>
          <svg viewBox="0 0 12 12" aria-hidden="true"><path d="M2 1.5 L4 1.5 L5 4 L3.8 5 C4.5 6.6 5.6 7.7 7 8.3 L8 7 L10.5 8 L10.5 10 C6 10.5 1.5 6 2 1.5 Z"/></svg>
          <span>415-555-0186</span>
        </li>
        <li>
          <svg viewBox="0 0 12 12" aria-hidden="true"><rect x="3" y="1" width="6" height="10" rx="1"/><line x1="5.2" y1="9.2" x2="6.8" y2="9.2"/></svg>
          <span>707-5550143</span>
        </li>
        <li>
          <svg viewBox="0 0 12 12" aria-hidden="true"><rect x="1" y="2.5" width="10" height="7"/><polyline points="1,2.5 6,6.5 11,2.5"/></svg>
          <span>info@talviquehotels.com</span>
        </li>
        <li>
          <svg viewBox="0 0 12 12" aria-hidden="true"><circle cx="6" cy="6" r="5"/><ellipse cx="6" cy="6" rx="2.2" ry="5"/><line x1="1" y1="6" x2="11" y2="6"/></svg>
          <span>www.talviquehotels.com</span>
        </li>
      </ul>
    </div>
  </section>
</main>
</body>
</html>
```